Redesign for a start up airline technology. The website is quelbrion.com.

I need a PowerPoint template that complements our website. I can provide our current template as a starting point.

```html
<!DOCTYPE html>
<html lang="en">
<head>
<meta charset="utf-8">
<title>Quelbrion Presentation Template</title>
<link rel="stylesheet" href="https://fonts.googleapis.com/css2?family=Exo+2:wght@300;400;600;700&family=Saira+Semi+Condensed:wght@700;800&display=swap">
<style>
:root{
  --stage:#8a8d90;
  --blue:#0b5c96;
  --green:#7ab92e;
  --navy:#1b3d7a;
  --sky:#29abe2;
  --ink:#3c4046;
  --muted:#6b7077;
  --line:#d9dce0;
  --badge:#0a5ca8;
  --white:#ffffff;
  --step1:#29b6e8;
  --step2:#8dc63f;
  --step3:#3b82e0;
  --step4:#22a84a;
  --track:#444a50;
}
*{margin:0;padding:0;box-sizing:border-box}
html,body{width:1043px;height:1200px;overflow:hidden;background:var(--stage)}
body{position:relative;font-family:"Exo 2",sans-serif;color:var(--ink)}
.slide{position:absolute;width:421px;height:237px;overflow:hidden;background:var(--white);box-shadow:0 4px 12px rgba(0,0,0,.28)}
.s1{left:92px;top:107px}.s2{left:92px;top:357px}.s3{left:92px;top:607px}.s4{left:92px;top:856px}
.s5{left:530px;top:107px}.s6{left:530px;top:357px}.s7{left:530px;top:607px}.s8{left:530px;top:856px}
.brand{position:absolute;font-family:"Exo 2",sans-serif;font-weight:700;color:var(--blue);letter-spacing:.2px}
.brand-corner{right:16px;top:15px;font-size:9px}
.heading{position:absolute;font-family:"Saira Semi Condensed","Arial Narrow",sans-serif;font-weight:800;color:var(--blue);letter-spacing:.4px;line-height:1;text-transform:uppercase}
.heading em{font-style:normal;color:var(--green)}
.page-no{position:absolute;left:398px;top:215px;width:16px;height:16px;border-radius:50%;background:radial-gradient(circle at 40% 35%,#2c86d0,var(--badge) 70%);color:#fff;font-size:5.5px;line-height:16px;text-align:center;font-weight:400}
.photo{position:absolute}
.body-copy{position:absolute;font-weight:300;color:var(--ink);text-align:justify}

/* slide 1 */
.s1 .photo{inset:0;background:linear-gradient(160deg,#ffffff 0%,#eef4fa 35%,#cfe2f3 65%,#9cc3e8 100%)}
.s1 .brand{left:0;right:0;top:36px;text-align:center;font-size:17px}
.s1 .heading{left:0;right:0;top:86px;text-align:center;font-size:23px}
.s1 .subtitle{position:absolute;left:0;right:0;top:119px;text-align:center;font-size:8px;font-weight:300;color:#333}

/* slide 2 */
.s2 .photo.backdrop{inset:0;background:linear-gradient(120deg,#eef3f8 0%,#f7f9fb 45%,#ffffff 100%)}
.s2 .heading{left:33px;top:50px;font-size:21px}
.agenda-list{position:absolute;left:34px;top:86px;list-style:none}
.agenda-list li{position:relative;padding-left:14px;font-size:7.6px;font-weight:300;line-height:16.6px;color:#333}
.agenda-list li::before{content:"";position:absolute;left:0;top:6px;width:4.5px;height:4.5px;border-radius:50%;background:var(--green)}
.agenda-ring{position:absolute;left:190px;top:25px}

/* slide 3 */
.s3 .heading{left:27px;top:35px;font-size:21px}
.s3 .body-copy{left:27px;top:67px;width:171px;font-size:5.7px;line-height:10.3px}
.s3 .photo{left:216px;top:43px;width:194px;height:160px;background:linear-gradient(180deg,#f0a35a 0%,#c77a45 35%,#4a5566 65%,#1f2630 100%)}

/* slide 4 */
.s4 .photo{inset:0;background:linear-gradient(180deg,#7fb6dd 0%,#b9d6ea 40%,#c9b9a6 70%,#8a8276 100%)}
.info-panel{position:absolute;left:12px;top:73px;width:215px;height:146px;background:#fff}
.info-panel .heading{left:16px;top:18px;font-size:21px;line-height:22px}
.info-panel .body-copy{left:16px;top:72px;width:185px;font-size:5.8px;line-height:10.3px}

/* slide 5 */
.s5 .heading,.s6 .heading,.s7 .heading{left:27px;top:20px;font-size:22px}
.flow{position:absolute;left:0;top:0}

/* slide 6 */
.data-table{position:absolute;left:23px;top:47px;width:374px;border-collapse:collapse;font-size:4.6px;color:var(--muted)}
.data-table th{background:var(--navy);color:#fff;font-weight:400;font-size:5.4px;height:18px;text-align:left;padding-left:14px;border-right:1px solid #fff}
.data-table th:nth-child(n+2){text-align:center;padding-left:0}
.data-table td{height:54.5px;border:.6px solid var(--line);padding:0 8px;line-height:7px;font-weight:300}
.data-table td:nth-child(n+2){text-align:center}
.data-table td:first-child{padding-left:9px}
.tick{width:6px;height:5px}

/* slide 7 */
.chart{position:absolute;left:29px;top:77px}
.s7 .body-copy{left:233px;width:172px;font-size:4.5px;line-height:7.2px;color:var(--muted)}
.s7 .para-one{top:77px}.s7 .para-two{top:142px}

/* slide 8 */
.s8 .photo{inset:0;background:linear-gradient(180deg,#1190d4 0%,#2aa2c2 45%,#3eae86 75%,#5bb24a 100%)}
.s8 .brand{left:0;right:0;top:68px;text-align:center;font-size:17px;color:#fff}
.s8 .heading{left:0;right:0;top:113px;text-align:center;font-size:23px;color:#fff}
.contact{position:absolute;left:0;right:0;text-align:center;color:#fff;font-size:8px;font-weight:300}
.contact svg{vertical-align:-1px;margin-right:6px}
.contact-address{top:155px}.contact-mail{top:168px}
</style>
</head>
<body>

<!-- 01 Title -->
<section class="slide s1">
  <div class="photo" role="img" aria-label="Passenger jet climbing through a bright blue sky with soft white clouds"></div>
  <div class="brand">Quelbrion</div>
  <h1 class="heading">Presentation <em>Title Here</em></h1>
  <p class="subtitle">Sed ut perspiciatis unde omnis isteit voluptatem</p>
  <div class="page-no">01</div>
</section>

<!-- 02 Agenda -->
<section class="slide s2">
  <div class="photo backdrop" role="img" aria-label="Faded airliner among pale clouds"></div>
  <div class="brand brand-corner">Quelbrion</div>
  <h2 class="heading">Our <em>Agenda</em></h2>
  <ul class="agenda-list">
    <li>Sed ut perspiciatis unde</li>
    <li>Omnis isteit voluptatem</li>
    <li>Duis aute irure dolor</li>
    <li>Rreprehenderitin</li>
    <li>Voluptate velit</li>
    <li>Eesse cillum dolore</li>
  </ul>
  <svg class="agenda-ring" width="180" height="180" viewBox="0 0 180 180">
    <defs>
      <radialGradient id="agendaPhoto" cx="55%" cy="45%" r="60%">
        <stop offset="0" stop-color="#3f8fd6"/>
        <stop offset=".6" stop-color="#1d4f97"/>
        <stop offset="1" stop-color="#0d2a5c"/>
      </radialGradient>
    </defs>
    <path d="M61.3 11 A84 84 0 0 1 172.7 104.6" fill="none" stroke="var(--sky)" stroke-width="3"/>
    <path d="M168.9 118.7 A84 84 0 0 1 6.3 97.3" fill="none" stroke="var(--green)" stroke-width="3"/>
    <circle cx="90" cy="90" r="78" fill="#fff"/>
    <circle cx="90" cy="90" r="76" fill="url(#agendaPhoto)" role="img" aria-label="Hands on a laptop with glowing flight booking and world map interface"/>
  </svg>
  <div class="page-no">02</div>
</section>

<!-- 03 About -->
<section class="slide s3">
  <div class="brand brand-corner">Quelbrion</div>
  <h2 class="heading">About <em>Us</em></h2>
  <p class="body-copy">Quelbrion is an aerospace technology company that produces a game changing onboard weight and balance measurement system - the Gear Load Sensing System (GLSS). The GLSS hardware kit automatically calculates an aircraft's weight and center of gravity for each flight.<br>With numerous design, process and method patents, Quelbrion brings a unique combination of engineering innovation and certification expertise within the airline and aerospace industries.<br>The Quelbrion leadership team holds decades of airline and relevant aviation experience, including a FAA delegated authority in the areas of Electrical Systems and Certification Management as a Designated Engineering Representative (DER).</p>
  <div class="photo" role="img" aria-label="Airliner parked on the apron at sunset with cargo being loaded"></div>
  <div class="page-no">03</div>
</section>

<!-- 04 Commercial aviation -->
<section class="slide s4">
  <div class="photo" role="img" aria-label="Jet taking off over an airport gate with a ground tug and cargo carts at sunset"></div>
  <div class="brand brand-corner">Quelbrion</div>
  <div class="info-panel">
    <h2 class="heading">Commercial<br><em>Aviation</em></h2>
    <p class="body-copy">An innovative approach to weight and balance planning turns estimations into actuals. The Gear Load Sensing System unlocks the aircraft's untapped potential, optimizes load planning for more efficient flying and reduced fuel burn. GLSS technology provides continuous health monitoring for landing gear systems.</p>
  </div>
  <div class="page-no">04</div>
</section>

<!-- 05 How it works -->
<section class="slide s5">
  <div class="brand brand-corner">Quelbrion</div>
  <h2 class="heading">How It <em>Works</em></h2>
  <svg class="flow" width="421" height="237" viewBox="0 0 724 407" font-family="Exo 2, sans-serif">
    <!-- connected S-shaped track -->
    <g fill="none" stroke-width="13">
      <path class="track-start" d="M60 189 H222 C250 189 261 172 261 140" stroke="var(--track)"/>
      <path class="step-one" d="M261 140 A50 50 0 0 1 361 140 A50 50 0 0 1 311 190" stroke="var(--step1)"/>
      <path class="step-two" d="M311 190 A50 50 0 0 0 261 240 A50 50 0 0 0 361 240" stroke="var(--step2)"/>
      <path class="step-three" d="M361 240 A50 50 0 0 1 461 240 A50 50 0 0 1 411 290" stroke="var(--step3)"/>
      <path class="step-four" d="M411 290 A50 50 0 0 0 361 340 A50 50 0 0 0 461 340" stroke="var(--step4)"/>
      <path class="track-finish" d="M461 340 C461 306 470 288 502 288 H662" stroke="var(--track)"/>
    </g>
    <!-- number gaps -->
    <g fill="#fff">
      <rect x="348" y="122" width="26" height="36"/>
      <rect x="248" y="222" width="26" height="36"/>
      <rect x="448" y="222" width="26" height="36"/>
      <rect x="348" y="322" width="26" height="36"/>
    </g>
    <g stroke-width="3">
      <path d="M348 122 H374 M348 158 H374" stroke="var(--step1)"/>
      <path d="M248 222 H274 M248 258 H274" stroke="var(--step2)"/>
      <path d="M448 222 H474 M448 258 H474" stroke="var(--step3)"/>
      <path d="M348 322 H374 M348 358 H374" stroke="var(--step4)"/>
    </g>
    <g font-family="Saira Semi Condensed, Arial Narrow, sans-serif" font-weight="700" font-size="19" text-anchor="middle">
      <text x="361" y="147" fill="var(--step1)">01</text>
      <text x="261" y="247" fill="var(--step2)">02</text>
      <text x="461" y="247" fill="var(--step3)">03</text>
      <text x="361" y="347" fill="var(--step4)">04</text>
    </g>
    <g font-size="5.5" font-weight="700" text-anchor="middle">
      <text x="311" y="152" fill="var(--step1)">TEAMWORK</text>
      <text x="311" y="252" fill="var(--step2)">SECURITY</text>
      <text x="411" y="252" fill="var(--step3)">GLOBAL SCOPE</text>
      <text x="411" y="352" fill="var(--step4)">DIRECTION</text>
    </g>
    <g fill="none" stroke-width="1.5">
      <g stroke="var(--step1)"><circle cx="306" cy="133" r="2.6"/><circle cx="316" cy="133" r="2.6"/><circle cx="311" cy="130" r="2.6"/><path d="M302 143 v-4 h18 v4"/></g>
      <path d="M311 226 l6 2 v5 c0 5 -3 8 -6 9 c-3 -1 -6 -4 -6 -9 v-5 z" stroke="var(--step2)"/>
      <g stroke="var(--step3)"><circle cx="411" cy="234" r="7"/><path d="M404 234 h14 M411 227 c-4 4 -4 10 0 14 c4 -4 4 -10 0 -14"/></g>
      <g stroke="var(--step4)"><circle cx="411" cy="333" r="7"/><path d="M411 328 v10 M406 333 h10"/></g>
      <path d="M130 196 V290 C130 296 134 300 140 300 H158" stroke="var(--track)" stroke-width="1"/>
    </g>
    <path d="M158 297 l4 3 l-4 3 z" fill="var(--track)"/>
    <g font-size="4.6" font-weight="700" fill="#fff" text-anchor="middle">
      <text x="158" y="191">STARTING POINT</text>
      <text x="546" y="290">FINISH POINT</text>
    </g>
    <g font-size="4.2" fill="#444">
      <text x="388" y="126"><tspan font-weight="700" fill="var(--step1)">DESCRIPTION</tspan><tspan x="388" dy="6">Brief note on this stage and the</tspan><tspan x="388" dy="5">result it brings to the team</tspan><tspan x="388" dy="5">across every flight.</tspan></text>
      <text x="238" y="226" text-anchor="end"><tspan font-weight="700" fill="var(--step2)">DESCRIPTION</tspan><tspan x="238" dy="6">Brief note on this stage and the</tspan><tspan x="238" dy="5">result it brings to the team</tspan><tspan x="238" dy="5">across every flight.</tspan></text>
      <text x="486" y="226"><tspan font-weight="700" fill="var(--step3)">DESCRIPTION</tspan><tspan x="486" dy="6">Brief note on this stage and the</tspan><tspan x="486" dy="5">result it brings to the team</tspan><tspan x="486" dy="5">across every flight.</tspan></text>
      <text x="164" y="298"><tspan font-weight="700">DESCRIPTION</tspan><tspan x="164" dy="6">Brief note on this stage and the</tspan><tspan x="164" dy="5">result it brings to the team</tspan><tspan x="164" dy="5">across every flight.</tspan></text>
      <text x="338" y="326" text-anchor="end"><tspan font-weight="700" fill="var(--step4)">DESCRIPTION</tspan><tspan x="338" dy="6">Brief note on this stage and the</tspan><tspan x="338" dy="5">result it brings to the team</tspan><tspan x="338" dy="5">across every flight.</tspan></text>
      <text x="522" y="306"><tspan font-weight="700">DESCRIPTION</tspan><tspan x="522" dy="6">Brief note on this stage and the</tspan><tspan x="522" dy="5">result it brings to the team</tspan><tspan x="522" dy="5">across every flight.</tspan></text>
    </g>
  </svg>
  <div class="page-no">05</div>
</section>

<!-- 06 Table -->
<section class="slide s6">
  <div class="brand brand-corner">Quelbrion</div>
  <h2 class="heading">Our <em>Table</em></h2>
  <table class="data-table">
    <colgroup><col style="width:88px"><col style="width:77px"><col style="width:70px"><col style="width:70px"><col style="width:69px"></colgroup>
    <thead><tr><th>OMMODO</th><th>CONSEQUAT</th><th>DUIS</th><th>AUTE IRU</th><th>LOREM</th></tr></thead>
    <tbody>
      <tr><td>Sed ut perspiciatis unde omnis iste natus error sit voluptatem accusantium</td><td>Sed ut perspiciatis</td><td>123,Sed ut perspiciatis</td><td>213245</td><td><svg class="tick" viewBox="0 0 6 5"><path d="M.5 2.6 L2.2 4.2 L5.5 .8" fill="none" stroke="var(--green)" stroke-width="1"/></svg></td></tr>
      <tr><td>Sed ut perspiciatis unde omnis iste natus error sit voluptatem accusantium</td><td>Sed ut perspiciatis</td><td>123,Sed ut perspiciatis</td><td>213245</td><td><svg class="tick" viewBox="0 0 6 5"><path d="M.5 2.6 L2.2 4.2 L5.5 .8" fill="none" stroke="var(--green)" stroke-width="1"/></svg></td></tr>
      <tr><td>Sed ut perspiciatis unde omnis iste natus error sit voluptatem accusantium</td><td>Sed ut perspiciatis</td><td>123,Sed ut perspiciatis</td><td>213245</td><td><svg class="tick" viewBox="0 0 6 5"><path d="M.5 2.6 L2.2 4.2 L5.5 .8" fill="none" stroke="var(--green)" stroke-width="1"/></svg></td></tr>
    </tbody>
  </table>
  <div class="page-no">06</div>
</section>

<!-- 07 Graph -->
<section class="slide s7">
  <div class="brand brand-corner">Quelbrion</div>
  <h2 class="heading">Our <em>Graph</em></h2>
  <svg class="chart" width="190" height="108" viewBox="0 0 327 185">
    <g stroke="#dde0e4" stroke-width="1">
      <path d="M42 0V185M83 0V185M124 0V185M164 0V185M204 0V185M245 0V185M285 0V185M327 0V185"/>
      <path d="M0 0H327M0 17H327M0 34H327M0 50H327M0 67H327M0 84H327M0 100H327M0 117H327M0 134H327M0 150H327M0 167H327"/>
    </g>
    <path d="M1 0V184H327" fill="none" stroke="#2f3a44" stroke-width="2"/>
    <polyline points="0,182 42,150 83,82 124,82 164,65 204,99 245,82 285,15 327,65" fill="none" stroke="#f28c28" stroke-width="1.6"/>
    <polyline points="0,82 42,116 83,133 124,150 164,133 204,150 245,166 285,116 327,99" fill="none" stroke="#1a9a9a" stroke-width="1.6"/>
    <g fill="#e5432d"><circle cx="42" cy="150" r="4"/><circle cx="83" cy="82" r="4"/><circle cx="124" cy="82" r="4"/><circle cx="164" cy="65" r="4"/><circle cx="204" cy="99" r="4"/><circle cx="245" cy="82" r="4"/><circle cx="285" cy="15" r="4"/></g>
    <g fill="#1e3e5c"><circle cx="42" cy="116" r="4"/><circle cx="83" cy="133" r="4"/><circle cx="124" cy="150" r="4"/><circle cx="164" cy="133" r="4"/><circle cx="204" cy="150" r="4"/><circle cx="245" cy="166" r="4"/><circle cx="285" cy="116" r="4"/></g>
  </svg>
  <p class="body-copy para-one">Sed ut perspiciatis unde omnis iste natus error sit voluptatem accusantium doloremque laudantium, totam rem aperiam, eaque ipsa quae ab illo inventore veritatis et quasi architecto beatae vitae dicta sunt explicabo. Nemo enim ipsam voluptatem quia voluptas sit aspernatur aut odit aut fugit, sed quia consequuntur magni dolores eos qui ratione voluptatem sequi nesciunt. Neque porro quisquam est, qui dolorem ipsum quia dolor sit amet, consectetur, adipisci velit, sed quia non numquam eius modi tempora incidunt ut labore et dolore magnam aliquam quaerat voluptatem.</p>
  <p class="body-copy para-two">Sed ut perspiciatis unde omnis iste natus error sit voluptatem accusantium doloremque laudantium, totam rem aperiam, eaque ipsa quae ab illo inventore veritatis et quasi architecto beatae vitae dicta sunt explicabo. Nemo enim ipsam voluptatem quia voluptas sit aspernatur aut odit aut fugit, sed quia consequuntur magni dolores eos qui ratione voluptatem sequi nesciunt. Neque porro quisquam est, qui dolorem ipsum quia dolor sit amet, consectetur, adipisci velit, sed quia non numquam eius modi tempora incidunt ut labore et dolore magnam aliquam quaerat voluptatem.</p>
  <div class="page-no">07</div>
</section>

<!-- 08 Thank you -->
<section class="slide s8">
  <div class="photo" role="img" aria-label="Airliner in flight against a blue-to-green tinted cloudy sky"></div>
  <div class="brand">Quelbrion</div>
  <h2 class="heading">Thank You</h2>
  <p class="contact contact-address"><svg width="9" height="7" viewBox="0 0 9 7"><path d="M0 1 L3 0 L6 1 L9 0 V6 L6 7 L3 6 L0 7 Z" fill="#fff"/></svg>4170 Harwell Ave. Suite 220 Austin, Texas 78701</p>
  <p class="contact contact-mail"><svg width="8" height="6" viewBox="0 0 8 6"><rect width="8" height="6" fill="#fff"/><path d="M0 0 L4 3.4 L8 0" fill="none" stroke="#2aa2a8" stroke-width=".8"/></svg>info@quelbrion.com</p>
  <div class="page-no">08</div>
</section>

</body>
</html>
```